Maple n Brook - Contact/Landing Page

I need a landing page which will essentially be the page that customers will go to from the 'website' link on QTV listing. It will provide a short overview of services which need to be selectable. a little further down can capture some contact details followed by a large Submit Now button etc...

I have some icon/logo's that can be utilised at the bottom of the page as industry type references.

Target Market(s)

End of Lease Cleaning Services

Industry/Entity Type

Cleaning Service

Colors

Designer to choose colors to be used in the design.

Requirements
Must have
• As per description
Should not have
• Colours to match my website maplenbrook.com.au

```html
<!DOCTYPE html>
<html lang="en">
<head>
<meta charset="utf-8">
<title>Maple n Brook – End of Lease Cleaning</title>
<link href="https://fonts.googleapis.com/css2?family=Roboto+Condensed:wght@300;400;700&display=swap" rel="stylesheet">
<style>
:root{
  --brand-blue:#2d5fa9;
  --accent:#1e8fd8;
  --accent-dark:#1677c4;
  --ink:#1c1c1c;
  --muted:#555;
  --quote-bg:#eaf4fb;
  --field-border:#c9d3dc;
  --white:#fff;
}
*{box-sizing:border-box;margin:0;padding:0}
html,body{width:740px;height:1200px;overflow:hidden}
body{font-family:"Roboto Condensed",sans-serif;background:var(--white);position:relative;color:var(--ink)}
.page{position:relative;width:740px;height:1200px}

/* header */
.hero{position:absolute;left:0;top:0;width:740px;height:395px;background:var(--brand-blue)}
.nav-link{position:absolute;top:30px;height:24px;line-height:24px;font-size:17px;font-weight:700;color:var(--white);text-decoration:none;padding:0 4px}
.nav-link.active{background:var(--accent)}
.brand{position:absolute;left:0;width:740px;top:150px;text-align:center}
.brand-mark{display:block;margin:0 auto 14px;width:54px;height:54px;border-radius:50%;background:var(--accent)}
.brand-name{font-size:54px;font-weight:700;color:var(--white);letter-spacing:.5px}
.tagline{position:absolute;left:0;width:740px;top:328px;text-align:center;color:var(--white);font-size:31px;font-weight:700}

/* service cards */
.card{position:absolute;top:401px;width:238px;height:299px;background:var(--white);border:1px solid #ddd;box-shadow:0 1px 3px rgba(0,0,0,.12)}
.card-photo{position:absolute;left:6px;top:6px;width:226px;height:152px}
.card-notch{position:absolute;left:6px;top:122px;width:226px;height:38px}
.card-title{position:absolute;top:168px;left:0;width:100%;text-align:center;font-size:23px;font-weight:700}
.card-text{position:absolute;top:202px;left:14px;right:14px;text-align:center;font-size:11.5px;font-weight:300;line-height:17px;color:var(--muted)}
.select-btn{position:absolute;top:252px;left:73px;width:92px;height:26px;background:linear-gradient(var(--accent),var(--accent-dark));color:var(--white);font-size:12px;font-weight:700;display:flex;align-items:center;justify-content:center;gap:14px}
.select-btn svg{width:11px;height:11px}

/* quote */
.quote{position:absolute;left:0;top:706px;width:740px;height:331px;background:var(--quote-bg)}
.quote-title{position:absolute;left:89px;top:36px;font-size:26px;font-weight:700}
.field-label{position:absolute;left:89px;font-size:11px;line-height:30px}
.field{position:absolute;left:163px;width:253px;height:30px;background:var(--white);border:1px solid var(--field-border)}
.mail-icon{position:absolute;left:457px;top:145px;width:33px;height:33px;border-radius:8px;background:linear-gradient(#2fb3f5,#1a6fe0)}
.email-label{position:absolute;left:506px;top:140px;font-size:17px;font-weight:700;color:var(--accent)}
.email-address{position:absolute;left:506px;top:164px;font-size:17px;color:var(--ink)}
.submit-btn{position:absolute;left:457px;top:208px;width:118px;height:40px;background:linear-gradient(var(--accent),var(--accent-dark));color:var(--white);font-size:15px;font-weight:700;display:flex;align-items:center;justify-content:center}

/* partners */
.partners{position:absolute;left:0;top:1037px;width:740px;height:114px;background:var(--white)}
.arrow{position:absolute;top:48px;width:27px;height:27px;border:1px solid #555;border-radius:50%}
.arrow svg{position:absolute;left:8px;top:7px;width:10px;height:12px}
.badge{position:absolute}

/* footer */
.footer{position:absolute;left:0;top:1151px;width:740px;height:49px;background:var(--brand-blue);color:var(--white)}
.copyright{position:absolute;left:88px;top:17px;font-size:11.5px;font-weight:300}
.licence{position:absolute;left:356px;top:13px;font-size:17px;font-weight:700}
.social{position:absolute;left:637px;top:17px;width:14px;height:14px;border-radius:3px;background:var(--white)}
</style>
</head>
<body>
<div class="page">

  <header class="hero">
    <a class="nav-link active" style="left:88px">HOME</a>
    <a class="nav-link" style="left:151px">ABOUT</a>
    <a class="nav-link" style="left:487px">SERVICES</a>
    <a class="nav-link" style="left:575px">PARTNERS</a>
    <div class="brand">
      <span class="brand-mark"></span>
      <span class="brand-name">Maple n Brook</span>
    </div>
    <h1 class="tagline">End of Lease Cleaning | Licensed Pest Control</h1>
  </header>

  <section class="card" style="left:7px">
    <div class="card-photo" role="img" aria-label="Cleaning supplies: bucket, sponges, spray bottles and brooms" style="background:linear-gradient(135deg,#2f6fd0,#e8c23a 55%,#c9312f)"></div>
    <svg class="card-notch" viewBox="0 0 226 38" preserveAspectRatio="none"><polygon points="0,38 113,0 226,38" fill="#fff"/></svg>
    <h2 class="card-title">Cleaning</h2>
    <p class="card-text">All interior cleaning carried out to property management requirements</p>
    <div class="select-btn">SELECT
      <svg viewBox="0 0 12 12"><rect x="1" y="2" width="9" height="9" rx="1.5" fill="none" stroke="#fff" stroke-width="1.4"/><path d="M3.5 6.5l2 2 5-6" fill="none" stroke="#fff" stroke-width="1.6"/></svg>
    </div>
  </section>

  <section class="card" style="left:251px">
    <div class="card-photo" role="img" aria-label="Vacuum cleaner head on a beige carpet" style="background:linear-gradient(135deg,#c9c3b6,#e2ddd3 50%,#bdb7aa)"></div>
    <svg class="card-notch" viewBox="0 0 226 38" preserveAspectRatio="none"><polygon points="0,38 113,0 226,38" fill="#fff"/></svg>
    <h2 class="card-title">Carpet Cleaning</h2>
    <p class="card-text">Carpet Cleaning to Australian standard<br>As 3733:1995</p>
    <div class="select-btn">SELECT
      <svg viewBox="0 0 12 12"><rect x="1.5" y="1.5" width="9" height="9" rx="1.5" fill="none" stroke="#fff" stroke-width="1.4"/></svg>
    </div>
  </section>

  <section class="card" style="left:495px">
    <div class="card-photo" role="img" aria-label="Dead cockroach on a wooden floor" style="background:linear-gradient(135deg,#e7c79a,#d3a66a 55%,#b97f46)"></div>
    <svg class="card-notch" viewBox="0 0 226 38" preserveAspectRatio="none"><polygon points="0,38 113,0 226,38" fill="#fff"/></svg>
    <h2 class="card-title">Pest Control</h2>
    <p class="card-text">Mandatory requirement for pests on premises</p>
    <div class="select-btn">SELECT
      <svg viewBox="0 0 12 12"><rect x="1.5" y="1.5" width="9" height="9" rx="1.5" fill="none" stroke="#fff" stroke-width="1.4"/></svg>
    </div>
  </section>

  <section class="quote">
    <h2 class="quote-title">GET A QUOTE</h2>
    <label class="field-label" style="top:100px">First name</label><div class="field" style="top:100px"></div>
    <label class="field-label" style="top:141px">Sur name</label><div class="field" style="top:141px"></div>
    <label class="field-label" style="top:181px">Email</label><div class="field" style="top:181px"></div>
    <label class="field-label" style="top:222px">Phone</label><div class="field" style="top:222px"></div>
    <label class="field-label" style="top:262px">Subrub</label><div class="field" style="top:262px"></div>

    <div class="mail-icon">
      <svg viewBox="0 0 33 33" width="33" height="33"><rect x="7" y="10" width="19" height="13" fill="none" stroke="#fff" stroke-width="1.5"/><path d="M7 10l9.5 8 9.5-8M7 23l7-6M26 23l-7-6" fill="none" stroke="#fff" stroke-width="1.3"/></svg>
    </div>
    <div class="email-label">EMAIL</div>
    <div class="email-address">info@maplenbrook.com.au</div>
    <div class="submit-btn">SUBMIT</div>
  </section>

  <section class="partners">
    <div class="arrow" style="left:39px"><svg viewBox="0 0 10 12"><path d="M7 1L2 6l5 5" fill="none" stroke="#333" stroke-width="1.5"/></svg></div>
    <div class="badge" style="left:89px;top:38px;width:109px;height:45px;border-radius:5px;background:#111"></div>
    <div class="badge" style="left:236px;top:40px;width:144px;height:39px;background:linear-gradient(90deg,#2a3a8c,#d9263a 55%,#5b6aa8)"></div>
    <div class="badge" style="left:422px;top:36px;width:74px;height:47px;background:#1d3f8f"></div>
    <div class="badge" style="left:527px;top:39px;width:131px;height:38px;background:#6cab2a"></div>
    <div class="arrow" style="left:673px"><svg viewBox="0 0 10 12"><path d="M3 1l5 5-5 5" fill="none" stroke="#333" stroke-width="1.5"/></svg></div>
  </section>

  <footer class="footer">
    <p class="copyright">Maple n Brook © 2021. All Rights Reserved.</p>
    <p class="licence">Pest licence : 4187326</p>
    <span class="social"></span>
  </footer>

</div>
</body>
</html>
```